I have a logo and need to design the business card and stationery.
Updates

The uploaded logo image named as GREYMARSH CONSTRUCTION which is to be replaced to GREYMARSH CONTRACTS. Kindly add below details and submit the designs- Company name- Greymarsh Engineering Contracts LLP Name & Post- Kelvan Joshi (Designated Partner) Address- Block No.317, Wing C, Tulvo Trade Court, Manek Pural Road, Ruparel Industrial Estate, Goregaon(E), Mumbai - 400 063 Contact- +91 97415 60382 Email- kelvanjoshi@mailbrook.example Website- www.greymarshcontracts.example Contact for Letterhead- +91-22-28754193

Hi Tovin Rahul, We are liking your Design #28860835. We have suggested some changes which are mentioned in feedback. Kindly revert with it asap to finalize this design.

Colors

Designer to choose colors to be used in the design.

```html
<!DOCTYPE html>
<html lang="en">
<head>
<meta charset="utf-8">
<title>Greymarsh Contracts – Business Card</title>
<link href="https://fonts.googleapis.com/css2?family=Michroma&family=Roboto:wght@400;700&display=swap" rel="stylesheet">
<style>
  :root {
    --backdrop: #1c1c1c;
    --card: #f4f4f4;
    --card-edge: #d9d9d9;
    --tab: #3d3d3d;
    --ink-strong: #4a4a4a;
    --ink-soft: #8a8a8a;
    --ink-body: #5c5c5c;
  }
  * { margin: 0; padding: 0; box-sizing: border-box; }
  html, body { width: 1200px; height: 900px; overflow: hidden; }
  body {
    background: var(--backdrop);
    font-family: "Roboto", Arial, sans-serif;
    position: relative;
  }
  .business-card {
    position: absolute;
    left: 180px; top: 210px;
    width: 840px; height: 480px;
    background: linear-gradient(135deg, #ffffff 0%, var(--card) 60%, #ececec 100%);
    border-bottom: 6px solid var(--card-edge);
    box-shadow: 0 18px 40px rgba(0,0,0,.55);
  }
  .card-tab {
    position: absolute;
    left: 0; top: 44px;
    width: 14px; height: 50px;
    background: var(--tab);
  }
  .contact-block {
    position: absolute;
    left: 64px; top: 70px;
    width: 400px;
  }
  .person-name {
    font-family: "Michroma", "Roboto", sans-serif;
    font-size: 27px;
    font-weight: 400;
    color: var(--ink-strong);
    letter-spacing: 1px;
    line-height: 1.1;
    white-space: nowrap;
  }
  .person-role {
    font-size: 22px;
    color: var(--ink-soft);
    margin-top: 4px;
  }
  .contact-list {
    list-style: none;
    margin-top: 34px;
    font-size: 17px;
    color: var(--ink-soft);
    line-height: 1.5;
  }
  .contact-list li { display: flex; align-items: center; gap: 10px; white-space: nowrap; }
  .contact-list svg { width: 15px; height: 15px; fill: var(--ink-strong); flex: none; }
  .company-address {
    margin-top: 14px;
    font-size: 16.5px;
    color: var(--ink-body);
    line-height: 1.45;
    font-style: normal;
    white-space: nowrap;
  }
  .company-name { font-weight: 700; color: var(--ink-strong); }
  .brand-mark {
    position: absolute;
    right: 70px; top: 170px;
    width: 290px;
    display: flex; flex-direction: column; align-items: center; gap: 18px;
  }
  .brand-square {
    width: 70px; height: 70px;
    border: 8px solid var(--ink-strong);
  }
  .brand-name {
    font-family: "Roboto", Arial, sans-serif;
    font-weight: 700;
    font-size: 22px;
    letter-spacing: 2px;
    color: var(--ink-strong);
    white-space: nowrap;
  }
</style>
</head>
<body>
  <section class="business-card">
    <div class="card-tab"></div>

    <div class="contact-block">
      <h1 class="person-name">KELVAN JOSHI</h1>
      <p class="person-role">Designated Partner</p>

      <ul class="contact-list">
        <li>
          <svg viewBox="0 0 16 16" aria-hidden="true"><path d="M3 1l3 3-1.5 2a9 9 0 0 0 5.5 5.5L12 10l3 3-2 2C7 15 1 9 1 3z"/></svg>
          +91 97415 60382 &nbsp;|&nbsp; +91-22-28754193
        </li>
        <li>
          <svg viewBox="0 0 16 16" aria-hidden="true"><path d="M1 3h14v10H1z M1 3l7 6 7-6" fill="none" stroke="#4a4a4a" stroke-width="1.6"/></svg>
          kelvanjoshi@mailbrook.example
        </li>
        <li>
          <svg viewBox="0 0 16 16" aria-hidden="true"><circle cx="8" cy="8" r="7"/></svg>
          www.greymarshcontracts.example
        </li>
      </ul>

      <address class="company-address">
        <span class="company-name">Greymarsh Engineering Contracts LLP</span><br>
        Block No.317, Wing C, Tulvo Trade Court,<br>
        Manek Pural Road, Ruparel Industrial Estate,<br>
        Goregaon(E), Mumbai - 400 063
      </address>
    </div>

    <div class="brand-mark">
      <div class="brand-square"></div>
      <span class="brand-name">GREYMARSH CONTRACTS</span>
    </div>
  </section>
</body>
</html>
```